Website Development for vaultmerrow.com.au

Build a new Wordpress/Responsive website for vaultmerrow.com.au

Target Market(s)

Compliance Managers, Risk Managers, Information Security and Cyber Security Professionals, Chief Data/Digital Officers, Chief Operating/Financial Officers, Business Continuity Professionals, Disaster Recovery Planners, Small Business Owners, Local/Federal Government entities

Industry/Entity Type

Data Service

Coding

Coded - Design and coding required

Number of Pages Required

5+ page

Font styles to use
Sans Serif

Colors

Designer to choose colors to be used in the design.

Requirements
Must have
• 1. Site Structure: Home Page plus the following chapter-pages for a) Services b) About c) Resources d) Blog e) Contact Us
• 2. Prefer site to built on wordpress and we can purchase a theme if needed (we currently use Kelp9 for other sites)
• 3. Blog needs to be wordpress based
• 4. We will host the site ourselves on our own servers
• 5. Responsive Design
Nice to have
• 1. Livechat capability/interface
• 2. Capability for marketing automation integration (such as hubspot, marketo, infusionsoft etc)
• 3. Capability for CRM integration (Salesforce)

```html
<!DOCTYPE html>
<html lang="en">
<head>
<meta charset="utf-8">
<title>Vaultmerrow – Visualizing Data To Build Climate Resilience</title>
<link href="https://fonts.googleapis.com/css2?family=Roboto:wght@300;400;500;700&display=swap" rel="stylesheet">
<style>
:root{
  --blue:#1b63b5;
  --blue-dark:#0f4a8f;
  --blue-deep:#0b3a78;
  --blue-light:#e8f1fb;
  --ink:#222;
  --text:#555;
  --muted:#888;
  --line:#d7dde5;
  --grey-bar:#5b6068;
  --footer:#7f8287;
  --white:#fff;
}
*{box-sizing:border-box;margin:0;padding:0}
html,body{width:1200px;height:4306px;overflow:hidden}
body{font-family:'Roboto',sans-serif;color:var(--text);background:var(--white);position:relative}
section,header,footer,.abs{position:absolute}
.brand{display:flex;align-items:center;gap:10px;font-weight:700;color:var(--blue);font-size:34px;letter-spacing:.5px}
.brand-dot{width:26px;height:26px;border-radius:50%;background:var(--blue)}
.brand.light{color:var(--white)}
.brand.light .brand-dot{background:var(--white)}

/* top bar */
.top-bar{top:0;left:0;width:1200px;height:57px;background:var(--grey-bar);color:#e8e8e8;font-size:15px}
.top-bar .contact{position:absolute;left:143px;top:19px;display:flex;gap:30px}
.top-bar .follow{position:absolute;right:143px;top:17px;display:flex;align-items:center;gap:8px;font-weight:500}
.social-sq{width:22px;height:22px;border-radius:3px;background:#8fa3bd;display:inline-block}

/* nav */
.site-nav{top:57px;left:0;width:1200px;height:80px;background:var(--white);box-shadow:0 2px 6px rgba(0,0,0,.08)}
.site-nav .brand{position:absolute;left:143px;top:20px}
.menu{position:absolute;right:140px;top:0;display:flex;height:80px;list-style:none;font-size:14px;font-weight:500;color:#444}
.menu li{padding:0 15px;line-height:80px}
.menu li.active{color:var(--blue);border-bottom:3px solid var(--blue)}

/* hero */
.hero{top:137px;left:0;width:1200px;height:463px;background:radial-gradient(ellipse at 50% 30%,#9fd4ff 0%,#3d8ee6 30%,#1450a8 65%,#0b2d66 100%)}
.hero h1{position:absolute;width:100%;top:354px;text-align:center;color:var(--white);font-size:36px;font-weight:500;text-shadow:0 2px 6px rgba(0,0,0,.4)}
.hero .dots{position:absolute;top:430px;left:570px;display:flex;gap:14px}
.hero .dots span{width:22px;height:3px;background:rgba(255,255,255,.6)}
.hero .dots span:first-child{background:var(--white)}

/* about */
.about{top:600px;left:0;width:1200px;height:614px}
.about .photo{position:absolute;left:143px;top:80px;width:443px;height:448px;background:linear-gradient(135deg,#e9eef3,#b7c3cf 60%,#3a4656)}
.about .photo .brand{position:absolute;left:12px;top:10px;font-size:20px;color:var(--white)}
.about .photo .brand-dot{width:14px;height:14px;background:var(--white)}
.about h2{position:absolute;left:630px;top:125px;display:flex;align-items:center;gap:14px;font-size:32px;font-weight:500;color:#333}
.about .copy{position:absolute;left:628px;top:210px;width:430px;font-size:12.5px;line-height:1.6}
.about .copy p{margin-bottom:10px}
.about .copy b{color:var(--blue);font-weight:500}
.about .cta{font-size:15px;color:#333;font-weight:500}
.about .cta a{color:var(--blue);font-weight:400;text-decoration:none}

/* section titles */
.sec-title{position:absolute;width:100%;text-align:center;font-size:38px;font-weight:500;color:#222}
.sec-lead{position:absolute;left:200px;width:800px;text-align:center;font-size:13px;line-height:1.7}
.sec-lead b{color:var(--blue);font-weight:400}

/* services */
.services{top:1214px;left:0;width:1200px;height:572px;background:var(--blue-light);overflow:hidden}
.services .sec-title{top:52px}
.services .sec-lead{top:120px}
.arc{position:absolute;border-radius:50%;background:#f4f8fd}
.arc.outer{left:230px;top:300px;width:740px;height:740px;background:#eef4fb}
.arc.inner{left:414px;top:309px;width:372px;height:372px;background:var(--white)}
.services .hub{position:absolute;left:500px;top:470px}
.svc-icon{position:absolute;width:104px;height:104px;border-radius:50%;background:var(--white);border:5px solid #4a4f57;display:flex;align-items:center;justify-content:center}
.svc-icon.active{border-color:var(--blue)}
.svc-label{position:absolute;font-size:15px;line-height:1.35;color:#333}
.svc-label.active{color:var(--blue)}

/* audience */
.audience{top:1786px;left:0;width:1200px;height:562px}
.audience .sec-title{top:100px}
.audience .sec-lead{top:160px}
.aud-circle{position:absolute;width:144px;height:144px;border-radius:50%;border:2px solid #e3e6ea;background:var(--white);display:flex;align-items:center;justify-content:center;box-shadow:0 3px 8px rgba(0,0,0,.06)}
.aud-circle.active{border:6px solid var(--blue)}
.aud-label{position:absolute;width:170px;text-align:center;font-size:16px;line-height:1.35;color:#444}
.aud-label.active{color:var(--blue)}
.arrow-btn{position:absolute;width:32px;height:32px;border-radius:50%;background:var(--white);border:1px solid #ccc;display:flex;align-items:center;justify-content:center}

/* team */
.team{top:2348px;left:0;width:1200px;height:652px;background:linear-gradient(180deg,#1a62b3,#0f4c96)}
.team .sec-title{top:80px;color:var(--white)}
.team .sub{position:absolute;top:138px;width:100%;text-align:center;color:#cfe2f7;font-size:20px}
.team-card{position:absolute;top:186px;width:160px;height:380px;background:var(--white);border-bottom:6px solid var(--blue)}
.team-card .pic{margin:14px 14px 0;height:200px;background:linear-gradient(180deg,#c9d3dd,#6d7a88)}
.team-card h3{text-align:center;font-size:14px;font-weight:400;color:#333;margin-top:18px}
.team-card.active h3{color:var(--blue)}
.team-card .role{text-align:center;font-size:11.5px;color:var(--muted);margin-top:4px}
.team-card .links{display:flex;gap:7px;justify-content:center;margin-top:10px}
.team-card .links span{width:8px;height:8px;border-radius:50%;background:#666}
.team .arrow-btn{background:rgba(255,255,255,.95);border:none}

/* blog */
.blog{top:3000px;left:0;width:1200px;height:648px;background:linear-gradient(180deg,#eef4fb,#e1ecf8)}
.blog .sec-title{top:76px}
.post{position:absolute;top:200px;width:437px;height:272px;background:var(--white);border-bottom:7px solid var(--blue);box-shadow:0 4px 10px rgba(0,0,0,.08);text-align:center}
.post .date{position:absolute;left:168px;top:-60px;width:100px;height:100px;border-radius:50%;background:var(--white);border:7px solid #6b7078;display:flex;flex-direction:column;align-items:center;justify-content:center;color:var(--blue)}
.post .date strong{font-size:40px;font-weight:500;line-height:1}
.post .date small{font-size:12px;color:#555}
.post h3{margin-top:70px;font-size:16px;font-weight:500;color:#222}
.post p{margin:18px auto 0;width:330px;font-size:12px;line-height:1.6;color:var(--muted)}
.post a{display:inline-block;margin-top:12px;font-size:13px;color:var(--blue);text-decoration:underline}
.btn-outline{position:absolute;left:524px;top:532px;width:152px;height:40px;border:1px solid #7fa6d6;background:var(--white);color:var(--blue);font-size:14px;display:flex;align-items:center;justify-content:center}
.blog .arrow-btn{top:318px}

/* contact */
.get-started{top:3648px;left:0;width:1200px;height:466px;background:linear-gradient(180deg,#2470c4,#1b5aa6)}
.get-started .sec-title{top:100px;color:var(--white)}
.form{position:absolute;left:314px;top:181px;width:640px;height:150px;display:grid;grid-template-columns:1fr 1fr}
.field{border:1px solid rgba(255,255,255,.35);color:#d9e7f7;font-size:13px;padding:14px 16px;height:50px}
.field.msg{grid-column:2;grid-row:1/4;height:150px}
.submit{position:absolute;left:526px;top:358px;width:148px;height:36px;background:#111;color:var(--white);font-size:14px;font-weight:500;display:flex;align-items:center;justify-content:center}
.chat-bubble{position:absolute;left:1016px;top:438px;width:56px;height:56px;border-radius:50%;background:var(--white);box-shadow:0 3px 8px rgba(0,0,0,.25);display:flex;align-items:center;justify-content:center;z-index:2}

/* footer */
.site-footer{top:4114px;left:0;width:1200px;height:192px;background:var(--footer);color:#f1f1f1}
.site-footer .brand{position:absolute;left:143px;top:62px}
.foot-menu{position:absolute;right:140px;top:86px;display:flex;gap:30px;list-style:none;font-size:13px}
.copyright{position:absolute;left:143px;right:143px;top:160px;display:flex;justify-content:space-between;font-size:12px;color:#e0e0e0}
</style>
</head>
<body>

<header class="top-bar">
  <div class="contact"><span>+000-555-019</span><span>info@vaultmerrow.com.au</span></div>
  <div class="follow">Follow Us on <span class="social-sq"></span><span class="social-sq"></span><span class="social-sq"></span><span class="social-sq"></span></div>
</header>

<nav class="site-nav abs">
  <div class="brand"><span class="brand-dot"></span>Vaultmerrow</div>
  <ul class="menu">
    <li class="active">HOME</li><li>ABOUT</li><li>SERVICES</li><li>RESOURCES</li><li>BLOG</li><li>CONTACT US</li>
  </ul>
</nav>

<section class="hero" role="img" aria-label="Glowing blue cloud network over circuit board lines">
  <h1>Visualizing Data To Build Climate Resilience</h1>
  <div class="dots"><span></span><span></span></div>
</section>

<section class="about">
  <div class="photo" role="img" aria-label="Smiling businessman in a suit working on a laptop">
    <div class="brand"><span class="brand-dot"></span>Vaultmerrow</div>
  </div>
  <h2>About <span class="brand"><span class="brand-dot"></span>Vaultmerrow</span></h2>
  <div class="copy">
    <p><b>Vaultmerrow</b> is a long established fact that a reader will be distracted by the readable content of a page when looking at its layout. The point of using Lorem Ipsum is that it has a more-or-less normal distribution.</p>
    <p>The point of using Lorem Ipsum is that it has a more-or-less normal distribution of letters, as opposed to using 'Content here, content here', making it look like readable English.</p>
    <p>Lorem Ipsum is that it has a more-or-less normal distribution of letters, as opposed to using 'Content here, content here', making it look like readable English has a more-or-less normal.</p>
    <p>The point of using Lorem Ipsum is that it has a more-or-less normal distribution of letters, as opposed to using 'Content here, content here', making it look like readable English.</p>
    <p class="cta">Get the support you need now. <a>Contact our 24/7 support line to get started.</a></p>
  </div>
</section>

<section class="services">
  <h2 class="sec-title">SERVICES</h2>
  <p class="sec-lead"><b>Vaultmerrow</b> is a long established fact that a reader will be distracted by the readable content of a page when looking at its layout. The point of using Lorem Ipsum is that it has a more-or-less normal distribution of letters.<br><br>The point of using Lorem Ipsum is that it has a more-or-less <b>Vaultmerrow</b> normal distribution of letters, as opposed to using 'Content here, content here', making it look like readable English.</p>
  <div class="arc outer"></div>
  <div class="arc inner"></div>
  <div class="brand hub"><span class="brand-dot"></span>Vaultmerrow</div>

  <div class="svc-icon active" style="left:448px;top:240px">
    <svg width="48" height="48" viewBox="0 0 48 48" fill="none" stroke="#1b63b5" stroke-width="2.5"><path d="M14 30a8 8 0 0 1 2-15 11 11 0 0 1 20 3 6 6 0 0 1-1 12z"/><rect x="19" y="22" width="10" height="8"/></svg>
  </div>
  <div class="svc-label active" style="left:272px;top:262px;text-align:right;width:160px">Data Management<br>Platforms</div>

  <div class="svc-icon" style="left:634px;top:240px">
    <svg width="48" height="48" viewBox="0 0 48 48" fill="none" stroke="#4a4f57" stroke-width="2.5"><circle cx="20" cy="20" r="7"/><circle cx="31" cy="31" r="5"/><path d="M20 9v4M20 27v4M9 20h4M27 20h4"/></svg>
  </div>
  <div class="svc-label" style="left:768px;top:280px">Industry Solutions</div>

  <div class="svc-icon" style="left:311px;top:368px">
    <svg width="48" height="48" viewBox="0 0 48 48" fill="none" stroke="#4a4f57" stroke-width="2.5"><ellipse cx="22" cy="13" rx="10" ry="4"/><path d="M12 13v20c0 2 4 4 10 4s10-2 10-4V13M12 23c0 2 4 4 10 4s10-2 10-4"/><circle cx="34" cy="34" r="5"/></svg>
  </div>
  <div class="svc-label" style="left:130px;top:392px;text-align:right;width:165px">Data Management<br>Services</div>

  <div class="svc-icon" style="left:777px;top:368px">
    <svg width="48" height="48" viewBox="0 0 48 48" fill="none" stroke="#4a4f57" stroke-width="2.5"><rect x="13" y="10" width="22" height="28" rx="2"/><rect x="19" y="22" width="10" height="9"/><path d="M21 22v-3a3 3 0 0 1 6 0v3"/></svg>
  </div>
  <div class="svc-label" style="left:896px;top:392px">Ransomware<br>Protection</div>
</section>

<section class="audience">
  <h2 class="sec-title">TO WHOM WE SERVE</h2>
  <p class="sec-lead">The point of using Lorem Ipsum is that it has a more-or-less normal distribution of letters, as opposed to using 'Content here, content here', making it look like readable English.</p>

  <div class="arrow-btn" style="left:75px;top:284px"><svg width="12" height="12" viewBox="0 0 12 12"><path d="M8 2 4 6l4 4" stroke="#777" stroke-width="2" fill="none"/></svg></div>
  <div class="arrow-btn" style="left:1092px;top:284px"><svg width="12" height="12" viewBox="0 0 12 12"><path d="m4 2 4 4-4 4" stroke="#777" stroke-width="2" fill="none"/></svg></div>

  <div class="aud-circle" style="left:142px;top:228px"><svg width="54" height="54" viewBox="0 0 54 54" fill="none" stroke="#555" stroke-width="2"><path d="M20 8 4 40h32z"/><path d="M20 20v10M20 34v2"/><circle cx="40" cy="38" r="7"/></svg></div>
  <div class="aud-label" style="left:129px;top:408px">Risk Managers</div>

  <div class="aud-circle" style="left:331px;top:228px"><svg width="54" height="54" viewBox="0 0 54 54" fill="none" stroke="#555" stroke-width="2"><path d="M27 6 44 12v14c0 12-8 18-17 22C18 44 10 38 10 26V12z"/><path d="m19 27 6 6 11-12"/></svg></div>
  <div class="aud-label" style="left:318px;top:408px">Information<br>Security</div>

  <div class="aud-circle active" style="left:520px;top:222px;width:156px;height:156px"><svg width="58" height="58" viewBox="0 0 58 58" fill="none" stroke="#1b63b5" stroke-width="2"><rect x="14" y="14" width="30" height="30" rx="3"/><rect x="22" y="22" width="14" height="14"/><path d="M20 6v8M29 6v8M38 6v8M20 44v8M29 44v8M38 44v8M6 20h8M6 29h8M6 38h8M44 20h8M44 29h8M44 38h8"/></svg></div>
  <div class="aud-label active" style="left:513px;top:408px">Cyber Security<br>Professionals</div>

  <div class="aud-circle" style="left:717px;top:228px"><svg width="54" height="54" viewBox="0 0 54 54" fill="none" stroke="#555" stroke-width="2"><circle cx="27" cy="16" r="7"/><path d="M15 34c0-7 5-11 12-11s12 4 12 11"/><path d="M8 38h38v6H8z"/></svg></div>
  <div class="aud-label" style="left:704px;top:408px">Chief Data<br>Technicians</div>

  <div class="aud-circle" style="left:908px;top:228px"><svg width="54" height="54" viewBox="0 0 54 54" fill="none" stroke="#555" stroke-width="2"><circle cx="27" cy="15" r="7"/><path d="M13 44c0-10 6-17 14-17s14 7 14 17z"/><path d="M27 27v17"/></svg></div>
  <div class="aud-label" style="left:895px;top:408px">Digital Officers</div>
</section>

<section class="team">
  <h2 class="sec-title">OUR TEAM</h2>
  <p class="sub">Our Bestest Team Members.</p>
  <div class="arrow-btn" style="left:143px;top:342px"><svg width="12" height="12" viewBox="0 0 12 12"><path d="M8 2 4 6l4 4" stroke="#1b63b5" stroke-width="2" fill="none"/></svg></div>
  <div class="arrow-btn" style="left:1023px;top:342px"><svg width="12" height="12" viewBox="0 0 12 12"><path d="m4 2 4 4-4 4" stroke="#1b63b5" stroke-width="2" fill="none"/></svg></div>

  <div class="team-card" style="left:191px">
    <div class="pic" role="img" aria-label="Portrait of team member Arlo"></div>
    <h3>ARLO</h3><p class="role">Designation Here</p>
    <div class="links"><span></span><span></span><span></span><span></span></div>
  </div>
  <div class="team-card active" style="left:400px">
    <div class="pic" role="img" aria-label="Portrait of team member Mira Colt"></div>
    <h3>MIRA COLT</h3><p class="role">Designation Here</p>
    <div class="links"><span></span><span></span><span></span><span></span></div>
  </div>
  <div class="team-card" style="left:606px">
    <div class="pic" role="img" aria-label="Portrait of team member Theo Barrat"></div>
    <h3>THEO BARRAT</h3><p class="role">Designation Here</p>
    <div class="links"><span></span><span></span><span></span><span></span></div>
  </div>
  <div class="team-card" style="left:814px">
    <div class="pic" role="img" aria-label="Portrait of team member Owen Pratley"></div>
    <h3>OWEN PRATLEY</h3><p class="role">Designation Here</p>
    <div class="links"><span></span><span></span><span></span><span></span></div>
  </div>
</section>

<section class="blog">
  <h2 class="sec-title">LATEST BLOG POSTS</h2>
  <div class="arrow-btn" style="left:84px"><svg width="12" height="12" viewBox="0 0 12 12"><path d="M8 2 4 6l4 4" stroke="#777" stroke-width="2" fill="none"/></svg></div>
  <div class="arrow-btn" style="left:1084px"><svg width="12" height="12" viewBox="0 0 12 12"><path d="m4 2 4 4-4 4" stroke="#777" stroke-width="2" fill="none"/></svg></div>

  <article class="post" style="left:143px">
    <div class="date"><strong>12</strong><small>Feb 2019</small></div>
    <h3>The point of using Lorem Ipsum</h3>
    <p>"The point of using Lorem Ipsum is that it has a more-or-less normal distribution of letters, as opposed to using Content here, content here, making it look like readable English letters, as opposed to using Content here, content here"</p>
    <a>Learn More</a>
  </article>
  <article class="post" style="left:614px">
    <div class="date"><strong>06</strong><small>Feb 2019</small></div>
    <h3>The point of using Lorem Ipsum</h3>
    <p>"The point of using Lorem Ipsum is that it has a more-or-less normal distribution of letters, as opposed to using Content here, content here, making it look like readable English letters, as opposed to using Content here, content here."</p>
    <a>Learn More</a>
  </article>
  <div class="btn-outline">View All</div>
</section>

<section class="get-started" role="img" aria-label="Blue-tinted photo of a team working together at desks">
  <h2 class="sec-title">LET'S GET STARTED</h2>
  <div class="form">
    <div class="field">Your Name</div>
    <div class="field msg">Your Message</div>
    <div class="field">Your Email</div>
    <div class="field">Your Contact Number</div>
  </div>
  <div class="submit">Submit</div>
  <div class="chat-bubble"><svg width="26" height="26" viewBox="0 0 26 26" fill="none" stroke="#1b63b5" stroke-width="2.2"><path d="M4 5h18v12H11l-5 4v-4H4z"/></svg></div>
</section>

<footer class="site-footer">
  <div class="brand light"><span class="brand-dot"></span>Vaultmerrow</div>
  <ul class="foot-menu"><li>HOME</li><li>ABOUT</li><li>SERVICES</li><li>RESOURCES</li><li>BLOG</li><li>CONTACT US</li></ul>
  <div class="copyright"><span>Copyright 2019 @ Vaultmerrow. All Rights Reserved.</span><span>Terms of services / Privacy Policy</span></div>
</footer>

</body>
</html>
```